Flyer-Design für psychologische Beratungspraxis für Mütter
Vielen herzlichen Dank! Super Kommunikation, alle Änderungswünsche wurden sofort umgesetzt, auch hin und her meinerseits war kein Problem, immer wieder. Schnelle Reaktion, tolle Ideen. Ich bin super zufrieden und würde jederzeit sehr gerne wieder mit brightfoxes zusammenarbeiten! Toller Flyer, ich liebe meinen neuen Flyer! :)
Zielgruppe
Gelassenheitswerkstatt ist eine psychologische Beratungspraxis. Ich unterstütze Mütter, Schwangere und Frauen mit Kinderwunsch bei Herausforderungen rund um Schwangerschaft, Geburt, Mutterschaft, und damit einhergehenden Problemen.
Aufgabenstellung
Text nochmal geringgradig geändert...siehe Datei anbei

```html
<!DOCTYPE html>
<html lang="de">
<head>
<meta charset="utf-8">
<title>Gelassenheitswerkstatt – Flyer</title>
<link href="https://fonts.googleapis.com/css2?family=Raleway:ital,wght@0,300;0,400;0,600;0,700;0,800;1,400&family=Caveat:wght@500&display=swap" rel="stylesheet">
<style>
:root{
  --navy:#243a7a;
  --navy-deep:#0f3a78;
  --green:#5aa82a;
  --orange:#e8542a;
  --ink:#2b2b2b;
  --paper:#ffffff;
  --bg:#ffffff;
  --shadow:rgba(0,0,0,.12);
  --sketch:#f4f4f4;
}
*{margin:0;padding:0;box-sizing:border-box}
html,body{width:874px;height:1200px;overflow:hidden;background:var(--bg)}
body{position:relative;font-family:"Raleway",sans-serif;color:var(--ink)}

/* brand header */
.brand-rule{position:absolute;left:0;top:120px;width:874px;height:40px}
.brand-mark{position:absolute;left:340px;top:62px;width:180px;text-align:center}
.brand-mark .dot{display:block;width:52px;height:52px;border-radius:50%;background:var(--orange);margin:0 auto 14px}
.brand-name{font-family:"Raleway",sans-serif;font-weight:700;color:var(--navy);line-height:1.1;letter-spacing:.02em}
.brand-mark .brand-name{font-size:15px}

.version{position:absolute;left:52px;font-weight:700;font-size:9px;color:#222}

/* panels */
.panel{position:absolute;left:32px;width:810px;height:276px;background:var(--paper);box-shadow:0 1px 6px var(--shadow);overflow:hidden}
.panel svg.curve{position:absolute;left:0;top:0;z-index:1}
.illus{position:absolute;z-index:0}
.headline,.copy,.when,.tagline,.practice,.contact,.flags,.signature,.offer-title,.offer-sub,.photo-brand,.mini{z-index:2}
.headline{position:absolute;font-weight:800;color:var(--navy);text-transform:uppercase;line-height:1.15;font-size:14px}
.copy{position:absolute;font-size:7.2px;line-height:10.8px;font-weight:300;color:var(--ink)}
.copy b{font-weight:700}
.copy .ln{display:block;white-space:nowrap}

.cover-title .l2{padding-left:13px}
.cover-copy{left:100px;top:101px;width:120px}
.cover-question{left:120px;top:158px;font-weight:600}

.tagline{position:absolute;left:300px;top:45px;font-family:"Caveat",cursive;font-weight:500;font-size:15px;color:var(--navy);transform:rotate(-6deg);line-height:13px}
.tagline .l2{padding-left:16px}
.portrait{position:absolute;left:412px;top:13px;width:87px;height:87px;border-radius:50%;background:radial-gradient(circle at 50% 30%,#dce8f2 0%,#b4c8dc 45%,#6f6a58 80%,#2d2a24 100%)}

.practice{position:absolute;left:260px;top:130px;width:285px;text-align:center;color:var(--navy)}
.practice .dot{display:block;width:22px;height:22px;border-radius:50%;background:var(--orange);margin:0 auto 6px}
.practice .brand-name{font-size:7px}
.practice .service{font-size:6.6px;font-weight:400;margin-top:11px;letter-spacing:.02em}
.practice .person{font-size:4.8px;margin-top:9px;letter-spacing:.02em}
.practice .role{font-size:4.8px;font-weight:700;margin-top:1px}
.contact{position:absolute;font-size:5px;color:var(--navy);line-height:10px;letter-spacing:.02em}
.contact .g{color:var(--green)}
.flags{position:absolute;left:442px;top:237px;display:flex;gap:3px}
.flag{width:10px;height:6px;display:flex}
.flag.de{flex-direction:column}
.flag i{flex:1}

.photo{position:absolute;left:537px;top:0;width:273px;height:200px}
.photo-brand{position:absolute;text-align:center}
.photo-brand .dot{display:block;border-radius:50%;background:var(--orange);margin:0 auto 5px}
.offer-title{position:absolute;left:537px;top:205px;width:273px;text-align:center;font-weight:800;font-size:14px;line-height:16px;color:var(--navy)}
.offer-sub{position:absolute;left:537px;top:242px;width:273px;text-align:center;font-weight:700;font-size:7px;line-height:9px;color:var(--green)}

/* inside spread */
.spread{top:883px;height:277px}
.col-blue{position:absolute;left:273px;top:0;width:269px;height:277px;background:var(--navy-deep)}
.spread .mini{position:absolute;left:18px;top:18px;width:46px;text-align:center}
.spread .mini .dot{display:block;width:15px;height:15px;border-radius:50%;background:var(--orange);margin:0 auto 3px}
.spread .mini .brand-name{font-size:4.2px}
.over-title{left:107px;top:18px}
.over-copy{left:107px;top:72px}
.over-copy2{left:134px;top:155px}
.when-title{left:294px;top:19px;color:#fff}
.when{position:absolute;font-size:7.2px;line-height:10.8px;color:#fff;font-weight:300;white-space:nowrap}
.when b{font-weight:700}
.yes-title{left:558px;top:18px}
.yes-copy{left:558px;top:57px}
.parent-title{left:574px;top:134px}
.parent-copy{left:574px;top:157px;width:206px}
.parent-copy p+p{margin-top:6px}
.signature{position:absolute;right:12px;top:254px;text-align:right;font-size:4.2px;line-height:5px;color:#444}
</style>
</head>
<body>

<svg class="brand-rule" viewBox="0 0 874 40" aria-hidden="true">
  <path d="M0 35 Q160 32 328 36" fill="none" stroke="var(--green)" stroke-width="1.6"/>
  <path d="M534 20 Q700 10 874 8" fill="none" stroke="var(--green)" stroke-width="1.6"/>
</svg>
<div class="brand-mark">
  <span class="dot"></span>
  <div class="brand-name">GELASSENHEITS<br>WERKSTATT</div>
</div>

<!-- V01 -->
<div class="version" style="top:247px">V01</div>
<section class="panel cover" style="top:266px">
  <div class="illus" role="img" aria-label="Linienzeichnung einer sitzenden schwangeren Frau" style="left:0;top:68px;width:96px;height:180px;background:linear-gradient(180deg,#fafafa,var(--sketch))"></div>
  <svg class="curve" width="810" height="276" aria-hidden="true"><path d="M0 244 L200 246 C262 248 283 215 285 160 L287 90 C288 72 292 66 302 65" fill="none" stroke="var(--green)" stroke-width="0.9"/></svg>
  <h2 class="headline cover-title" style="left:83px;top:52px">Mutter sein<br><span class="l2">ist wunderbar.</span></h2>
  <p class="copy cover-copy"><span class="ln">Wenn eine Frau Mutter wird, ist sie</span><span class="ln" style="padding-left:2px">plötzlich verliebt über beide</span><span class="ln" style="padding-left:9px">Ohren, unbändig stolz und von</span><span class="ln" style="padding-left:14px">Glücksgefühlen völlig über-</span><span class="ln" style="padding-left:17px">wältigt.</span></p>
  <p class="copy cover-question">So ist es doch „NORMAL“,<br>oder...?</p>
  <p class="tagline">Ich berate und<br><span class="l2">begleite Sie gerne.</span></p>
  <div class="portrait" role="img" aria-label="Porträtfoto der Beraterin an einem Wegweiser vor Himmel"></div>
  <div class="practice">
    <span class="dot"></span>
    <div class="brand-name">GELASSENHEITS<br>WERKSTATT</div>
    <div class="service">SYSTEMISCHE BERATUNG &amp; COACHING</div>
    <div class="person">DR. HELENA MARQUARDT</div>
    <div class="role">SYSTEMISCHE BERATERIN (DVSB) – HEILPRAKTIKERIN FÜR PSYCHOTHERAPIE</div>
  </div>
  <p class="contact" style="left:305px;top:227px">WWW.GELASSENHEITS<span class="g">WERKSTATT</span>.DE<br>INFO@GELASSENHEITS<span class="g">WERKSTATT</span>.DE</p>
  <p class="contact" style="left:432px;top:227px">TELEFON: 0152 480 17 305</p>
  <div class="flags" aria-hidden="true">
    <span class="flag de"><i style="background:#000"></i><i style="background:#d00"></i><i style="background:#fc0"></i></span>
    <span class="flag"><i style="background:#009246"></i><i style="background:#fff"></i><i style="background:#ce2b37"></i></span>
    <span class="flag"><i style="background:#012169"></i><i style="background:#c8102e"></i><i style="background:#012169"></i></span>
    <span class="flag"><i style="background:#0055a4"></i><i style="background:#fff"></i><i style="background:#ef4135"></i></span>
  </div>
  <div class="photo" role="img" aria-label="Gemaltes Foto einer Mutter neben ihrem schlafenden Neugeborenen" style="background:linear-gradient(180deg,rgba(255,255,255,0) 72%,#fff 100%),linear-gradient(90deg,#4b3a2a 0%,#a98460 35%,#c9d7d2 65%,#9fc2c6 100%)"></div>
  <div class="photo-brand" style="left:740px;top:12px;width:64px">
    <span class="dot" style="width:20px;height:20px"></span>
    <div class="brand-name" style="font-size:5.4px">GELASSENHEITS<br>WERKSTATT</div>
  </div>
  <h1 class="offer-title">KRISENBEGLEITUNG<br>UND LEBENSBERATUNG</h1>
  <p class="offer-sub">Psychologische Beratungspraxis für<br>Mütter, Schwangere und Frauen mit Kinderwunsch</p>
</section>

<!-- V02 -->
<div class="version" style="top:557px">V02</div>
<section class="panel cover" style="top:573px">
  <div class="illus" role="img" aria-label="Linienzeichnung einer sitzenden schwangeren Frau" style="left:0;top:68px;width:96px;height:180px;background:linear-gradient(180deg,#fafafa,var(--sketch))"></div>
  <svg class="curve" width="810" height="276" aria-hidden="true"><path d="M0 244 L200 246 C262 248 283 215 285 160 L287 90 C288 72 292 66 302 65" fill="none" stroke="var(--green)" stroke-width="0.9"/></svg>
  <h2 class="headline cover-title" style="left:83px;top:52px">Mutter sein<br><span class="l2">ist wunderbar.</span></h2>
  <p class="copy cover-copy"><span class="ln">Wenn eine Frau Mutter wird, ist sie</span><span class="ln" style="padding-left:2px">plötzlich verliebt über beide</span><span class="ln" style="padding-left:9px">Ohren, unbändig stolz und von</span><span class="ln" style="padding-left:14px">Glücksgefühlen völlig über-</span><span class="ln" style="padding-left:17px">wältigt.</span></p>
  <p class="copy cover-question">So ist es doch „NORMAL“,<br>oder...?</p>
  <p class="tagline">Ich berate und<br><span class="l2">begleite Sie gerne.</span></p>
  <div class="portrait" role="img" aria-label="Porträtfoto der Beraterin an einem Wegweiser vor Himmel"></div>
  <div class="practice">
    <span class="dot"></span>
    <div class="brand-name">GELASSENHEITS<br>WERKSTATT</div>
    <div class="service">SYSTEMISCHE BERATUNG &amp; COACHING</div>
    <div class="person">DR. HELENA MARQUARDT</div>
    <div class="role">SYSTEMISCHE BERATERIN (DVSB) – HEILPRAKTIKERIN FÜR PSYCHOTHERAPIE</div>
  </div>
  <p class="contact" style="left:305px;top:227px">WWW.GELASSENHEITS<span class="g">WERKSTATT</span>.DE<br>INFO@GELASSENHEITS<span class="g">WERKSTATT</span>.DE</p>
  <p class="contact" style="left:432px;top:227px">TELEFON: 0152 480 17 305</p>
  <div class="flags" aria-hidden="true">
    <span class="flag de"><i style="background:#000"></i><i style="background:#d00"></i><i style="background:#fc0"></i></span>
    <span class="flag"><i style="background:#009246"></i><i style="background:#fff"></i><i style="background:#ce2b37"></i></span>
    <span class="flag"><i style="background:#012169"></i><i style="background:#c8102e"></i><i style="background:#012169"></i></span>
    <span class="flag"><i style="background:#0055a4"></i><i style="background:#fff"></i><i style="background:#ef4135"></i></span>
  </div>
  <div class="photo" role="img" aria-label="Gemaltes Foto einer Mutter, die mit ihrem Kleinkind im Sandkasten spielt" style="background:linear-gradient(180deg,rgba(255,255,255,0) 72%,#fff 100%),linear-gradient(160deg,#8a8f86 0%,#d8cbb4 35%,#c4503a 55%,#9aa3b5 75%,#e2d8c6 100%)"></div>
  <div class="photo-brand" style="left:690px;top:20px;width:110px">
    <span class="dot" style="width:32px;height:32px"></span>
    <div class="brand-name" style="font-size:7.4px">GELASSENHEITS<br>WERKSTATT</div>
  </div>
  <h1 class="offer-title">KRISENBEGLEITUNG<br>UND LEBENSBERATUNG</h1>
  <p class="offer-sub">Psychologische Beratungspraxis für<br>Mütter, Schwangere und Frauen mit Kinderwunsch</p>
</section>

<!-- inside spread -->
<section class="panel spread">
  <div class="col-blue"></div>
  <div class="illus" role="img" aria-label="Linienzeichnung einer Mutter mit Baby im Tragetuch" style="left:21px;top:44px;width:80px;height:210px;background:linear-gradient(180deg,#fafafa,var(--sketch))"></div>
  <div class="illus" role="img" aria-label="Linienzeichnung einer Mutter, die ihr Baby hält" style="left:278px;top:132px;width:46px;height:130px;background:linear-gradient(180deg,rgba(255,255,255,.05),rgba(255,255,255,.12))"></div>
  <div class="illus" role="img" aria-label="Linienzeichnung einer Mutter, die ihr Kind hochhebt" style="left:714px;top:13px;width:92px;height:118px;background:linear-gradient(180deg,#fafafa,var(--sketch))"></div>
  <svg class="curve" width="810" height="277" aria-hidden="true"><path d="M0 232 C18 256 44 252 50 240 C90 250 240 246 300 240 C400 232 460 232 515 218 C548 208 540 122 575 116 C620 108 680 116 730 122 L800 122" fill="none" stroke="var(--green)" stroke-width="0.9"/></svg>

  <div class="mini">
    <span class="dot"></span>
    <div class="brand-name">GELASSENHEITS<br>WERKSTATT</div>
  </div>
  <h2 class="headline over-title">Überforderung,<br>Frustration und<br>Verzweiflung</h2>
  <p class="copy over-copy"><span class="ln">kennen Mütter, Frauen mit Kinderwunsch und</span><span class="ln">werdende Mütter allerdings ebenfalls nur zu</span><span class="ln" style="padding-left:12px">gut. Wichtig ist, dass die Beurteilung einer</span><span class="ln" style="padding-left:24px">Situation, d.h. wie stark sie uns belastet</span><span class="ln" style="padding-left:28px">alleine uns selbst zusteht. Nur unsere</span><span class="ln" style="padding-left:28px">eigene <b>subjektive Einschätzung</b> ist</span><span class="ln" style="padding-left:28px">ausschlaggebend.</span></p>
  <p class="copy over-copy2"><span class="ln">So unterschiedlich wir Menschen</span><span class="ln" style="padding-left:2px">sind, so verschieden ist nämlich</span><span class="ln">auch unser persönliches Fühlen und</span><span class="ln">Erleben. Deshalb benötigen wir</span><span class="ln"><b>individuell passende Lösungen</b> für</span><span class="ln">unsere Herausforderungen.</span></p>

  <h2 class="headline when-title">Was also wenn...</h2>
  <p class="when" style="left:294px;top:38px">... wir gern <b>Mutter wären</b>, aber das Leben andere Pläne hat?</p>
  <p class="when" style="left:294px;top:53px">... uns die Erfahrung der <b>Geburt belastet</b>, aber niemand zuhört,<br>&nbsp;&nbsp;weil ja <i>„jetzt alles ok sei“</i>?</p>
  <p class="when" style="left:294px;top:79px">... wenn wir unser <b>Kind verloren</b> haben?</p>
  <p class="when" style="left:294px;top:94px">... unser Kind oder wir selbst mit einer <b>Krankheit</b> zu kämpfen haben?</p>
  <p class="when" style="left:326px;top:109px">... wir selbst oder unser Partner uns <b>kaum</b><br>wiedererkennen?</p>
  <p class="when" style="left:334px;top:135px">... wenn wir uns treu bleiben wollen aber uns dennoch<br>&nbsp;durch die Meinung anderer <b>verunsichern</b> lassen?</p>
  <p class="when" style="left:348px;top:161px">... wir eben <b>nicht stolz</b> darauf sind wie wir den<br>letzten Schreianfall unseres Baby begleitet haben?</p>
  <p class="when" style="left:354px;top:186px">... wir weder die <b>Wut</b> unseres Kindes, noch unsere<br>eigene Wut gebändigt bekommen?</p>
  <p class="when" style="left:350px;top:212px">... wir mit der Situation <b>überfordert</b> sind und nicht<br>&nbsp;&nbsp;mehr weiter wissen?</p>

  <h2 class="headline yes-title">Ja, Mutter sein ist<br>wundervoll!</h2>
  <p class="copy yes-copy"><span class="ln">Und ja, die Dynamik der Paarbeziehung ver-</span><span class="ln">ändert sich schlagartig und wir stehen plötz-</span><span class="ln">lich vor einer der erfüllendsten Aufgaben und</span><span class="ln">zugleich einer der größten <b>existentiellen</b></span><span class="ln"><b>Herausforderungen</b> die uns das Leben bietet:</span></p>
  <h2 class="headline parent-title">Eltern sein.</h2>
  <div class="copy parent-copy">
    <p>Um trotz Rückschlägen ein zufriedenes Leben zu führen und um feinfühlig für unsere Kinder da zu sein, benötigen wir viel Kraft. Mentale Kraft, die es uns ermöglicht aus den Augen unserer Kinder zu sehen, unsere eigenen Gefühle zu regulieren und die starken Gefühle unserer Kinder auszuhalten und zu begleiten.</p>
    <p>Gemeinsam erarbeiten wir <b>individuelle Strategien</b>, wie Sie auf Ihre eigenen Ressourcen besser zugreifen, und so mental gestärkt nach vorne schauen können.</p>
  </div>
  <p class="signature">Dr. Helena Marquardt<br>Systemische Beraterin (DVSB) – Heilpraktikerin für Psychotherapie</p>
</section>

</body>
</html>
```